QuillVane needs a dashboard page designed

Redesign the dashboard shown in the provided images.

There are two images:
- dashboard.png
- dashboard-expanded.png

NOTE: The vocabulary navigation on the left will be a very long list of words 100s, so keep that in mind when you're designing both the vocab navigation and the expanded vocab popup.

In the dashboard.png picture, there needs to be a progress chart showing the word progress like the following: review 1(show it as completed) -> review 2(show the user they are here) -> review 3(unvisited) -> review 4(unvisited)

The do-not-design-this-page.png image is for your reference only. It is not to be designed. Use it to understand the overall look and feel of the website to help you create the best dashboard page possible.
Updates

Need extra days to review

Industry/Entity Type

Education English learning

Number of Pages Required

1 page

Requirements
Must have
• The main navigation and main header cannot change between pages. See the do-not-design page for the main navigateion and header.
Should not have
• Do not add a person profile. We will not have images of our users. Keep the icons in the main navigation as they are.

```html
<!DOCTYPE html>
<html lang="en">
<head>
<meta charset="utf-8">
<title>QuillVane – Word Progress Dashboard</title>
<link href="https://fonts.googleapis.com/css2?family=Poppins:wght@400;500;600;700;800&display=swap" rel="stylesheet">
<style>
:root{
  --brand:#2f67b3;
  --brand-deep:#2b5fae;
  --nav-tile:#4a80c2;
  --panel:#2c5184;
  --accent:#2a62b2;
  --ink:#1d1d1f;
  --muted:#3a3a3a;
  --grey-step:#bdbdbd;
  --bar-idle:#e6e6e6;
  --band-long:#f4f6f9;
  --band-work:#eef4f2;
  --band-short:#f8f8ea;
  --band-forgot:#f3f3f3;
  --chip:#e9edf6;
  --white:#ffffff;
}
*{box-sizing:border-box;margin:0;padding:0}
html,body{width:822px;height:1200px;overflow:hidden;background:var(--white);font-family:'Poppins',sans-serif;color:var(--ink)}
.screen{position:absolute;left:66px;width:1338px;height:976px;background:var(--brand);transform:scale(0.5157);transform-origin:0 0;overflow:hidden}
.screen--main{top:68px}
.screen--popup{top:628px}
.abs{position:absolute}
.brand-name{left:26px;top:14px;font-size:24px;font-weight:700;color:var(--white)}
.topbar-title{left:461px;top:8px;font-size:15px;font-weight:500;color:var(--white)}
.topbar-title svg{vertical-align:middle;margin-left:4px}
.topbar-icons{left:1105px;top:11px;display:flex;gap:8px}
.topbar-icons span{width:17px;height:17px;border-radius:50%;background:var(--white);display:flex;align-items:center;justify-content:center}
.topbar-icons i{width:7px;height:7px;border-radius:50%;background:var(--brand)}
.search{left:1214px;top:11px;width:73px;height:17px;background:var(--white);font-size:7px;color:#555;padding:3px 6px;display:flex;justify-content:space-between}
.search-caret{left:1294px;top:12px;color:var(--white);font-size:9px}

.main-nav{left:21px;top:61px;width:118px;height:849px;background:var(--nav-tile);border-radius:20px;overflow:hidden}
.nav-item{height:92px;display:flex;flex-direction:column;align-items:center;justify-content:center;gap:6px;color:var(--white);font-size:13px;font-weight:600;border-bottom:1px solid rgba(255,255,255,.35)}
.nav-item--active{background:var(--white);color:var(--accent);height:84px;border-radius:20px 20px 0 0;border:none}
.nav-item--biz{height:96px}

.vocab-panel{left:159px;top:62px;width:224px;height:847px;background:var(--panel);border:2px solid var(--white);border-radius:20px;color:var(--white)}
.filter{width:54px;height:21px;background:var(--white);color:var(--accent);font-size:12px;font-weight:600;border-radius:2px;display:flex;align-items:center;justify-content:center;gap:6px}
.vocab-panel .filter{left:16px;top:20px}
.expand{left:136px;top:20px;font-size:13px;font-weight:500}
.group-icon{width:30px;height:30px;border-radius:50%;border:2px solid var(--white);display:flex;align-items:center;justify-content:center;left:20px}
.group-title{left:59px;font-size:11px;font-weight:600}
.help{left:196px;width:11px;height:11px;border-radius:50%;background:var(--white);color:var(--panel);font-size:8px;font-weight:700;text-align:center;line-height:11px}
.word{left:60px;font-size:11px}
.word--lead{font-size:13px}

.content{left:405px;top:39px;width:928px;height:931px;background:var(--white)}
.h-progress{left:31px;top:20px;font-size:17px;font-weight:600}
.track{top:91px;height:2px}
.step{width:44px;height:44px;border-radius:50%;color:var(--white);font-size:24px;font-weight:700;display:flex;align-items:center;justify-content:center;border:3px solid var(--white);box-shadow:0 0 0 2px currentColor}
.step--done,.step--current{background:var(--accent);box-shadow:0 0 0 2px var(--accent)}
.step--todo{background:var(--grey-step);box-shadow:0 0 0 2px var(--grey-step)}
.step-label{top:129px;font-size:15px;font-weight:600;color:var(--accent)}
.step-label--todo{color:#a9a9a9}
.btn-continue{left:390px;top:106px;width:154px;height:30px;border-radius:15px;background:var(--accent);color:var(--white);font-size:12px;font-weight:600;display:flex;align-items:center;justify-content:center}
.btn-start{left:27px;top:206px;width:324px;height:35px;border:2px solid var(--accent);border-radius:18px;color:var(--accent);font-size:15px;font-weight:600;display:flex;align-items:center;justify-content:center;gap:8px}
.chip-word{left:369px;top:206px;width:91px;height:33px;border-radius:17px;background:var(--chip);color:var(--accent);font-size:15px;font-weight:600;display:flex;align-items:center;justify-content:center;gap:6px}
.definition{left:28px;top:268px;width:870px;font-size:12.3px;line-height:26px;color:var(--ink)}
.definition b{color:var(--accent);font-weight:600}
.definition strong{color:var(--ink);font-weight:600}
.h-curve{left:30px;top:380px;font-size:20px;font-weight:600;color:var(--accent)}
.chart{left:27px;top:436px;width:872px;height:258px;border:2px solid #dcdcdc;border-radius:20px;overflow:hidden}
.band{left:0;width:100%}
.band-label{left:5px;font-size:8.5px;color:var(--muted)}
.bar{width:13px;border-radius:7px 7px 0 0;background:var(--bar-idle);bottom:0}
.bar--hit{background:var(--accent)}
.tip{background:var(--white);border:1px solid #e3e3e3;font-size:11px;font-weight:500;color:var(--accent);width:64px;height:26px;display:flex;align-items:center;justify-content:center}
.axis{left:33px;top:705px;width:858px;display:flex;justify-content:space-between;font-size:8.5px;color:var(--muted)}
.axis-title{left:466px;top:725px;font-size:10px;font-weight:600;color:var(--accent)}
.h-analysis{left:28px;top:772px;font-size:16.5px;font-weight:700}
.analysis{left:28px;top:813px;width:870px;font-size:12.3px;line-height:24px;color:var(--muted)}

.scrim{inset:0;background:rgba(47,103,179,.74)}
.modal{left:242px;top:290px;width:854px;height:396px;background:var(--white);border-radius:14px}
.modal-frame{inset:12px;border:3px solid var(--accent);border-radius:14px}
.modal .filter{left:52px;top:40px;width:64px;height:23px;background:var(--accent);color:var(--white)}
.close{left:800px;top:33px}
.group-head{left:49px;width:273px;height:33px;background:var(--chip);font-size:17px;font-weight:500;padding-left:19px;line-height:33px}
.word-row{left:72px;display:flex;gap:18px;font-size:14px;color:var(--muted)}
</style>
</head>
<body>

<!-- ===== Dashboard view ===== -->
<section class="screen screen--main">
  <div class="abs brand-name">QuillVane</div>
  <div class="abs topbar-title">WordNest Tutor<svg width="10" height="6" viewBox="0 0 10 6"><path d="M0 0h10L5 6z" fill="#fff"/></svg></div>
  <div class="abs topbar-icons"><span><i></i></span><span><i></i></span><span><i></i></span><span><i></i></span></div>
  <div class="abs search"><span>Search</span><span>⌕</span></div>
  <div class="abs search-caret">⌄</div>

  <nav class="abs main-nav">
    <div class="nav-item nav-item--active">
      <svg width="28" height="26" viewBox="0 0 28 26"><path d="M14 1 1 13h4v12h7v-8h4v8h7V13h4z" fill="#2a62b2"/></svg>
      WordNest Tutor</div>
    <div class="nav-item">
      <svg width="32" height="30" viewBox="0 0 32 30"><path d="M1 8l9-3 10 3 8-3v22l-8 3-10-3-9 3z" fill="#fff"/><path d="M10 5v22M20 8v22" stroke="#4a80c2" stroke-width="2"/><circle cx="24" cy="6" r="5" fill="#fff" stroke="#4a80c2" stroke-width="2"/></svg>
      Daily English</div>
    <div class="nav-item nav-item--biz">
      <svg width="34" height="32" viewBox="0 0 34 32"><circle cx="13" cy="12" r="9" fill="none" stroke="#fff" stroke-width="5" stroke-dasharray="4 3"/><circle cx="13" cy="12" r="4" fill="#fff"/><circle cx="25" cy="23" r="6" fill="none" stroke="#fff" stroke-width="4" stroke-dasharray="3 2"/></svg>
      Business</div>
  </nav>

  <aside class="abs vocab-panel">
    <div class="abs filter">All <svg width="9" height="6" viewBox="0 0 9 6"><path d="M1 1l3.5 3.5L8 1" stroke="#2a62b2" stroke-width="1.6" fill="none"/></svg></div>
    <div class="abs expand">Expand <svg width="13" height="13" viewBox="0 0 13 13"><path d="M6 2H1v10h10V7M8 1h4v4M12 1 6 7" stroke="#fff" stroke-width="1.4" fill="none"/></svg></div>

    <div class="abs group-icon" style="top:66px"><svg width="14" height="14" viewBox="0 0 14 14"><circle cx="7" cy="7" r="6" fill="#fff"/><path d="M7 3v4l2 2" stroke="#2c5184" stroke-width="1.5" fill="none"/></svg></div>
    <div class="abs group-title" style="top:73px">Short-Term Memory</div><div class="abs help" style="top:76px">?</div>
    <div class="abs word word--lead" style="top:99px">Grab</div>

    <div class="abs group-icon" style="top:130px"><svg width="14" height="14" viewBox="0 0 14 14"><rect x="3" y="3" width="8" height="8" fill="#fff"/><path d="M5 0v14M9 0v14M0 5h14M0 9h14" stroke="#fff" stroke-width="1"/></svg></div>
    <div class="abs group-title" style="top:137px">Working Memory</div><div class="abs help" style="top:140px">?</div>
    <div class="abs word" style="top:164px">Cool Down</div>
    <div class="abs word" style="top:185px">Crave</div>
    <div class="abs word" style="top:206px">Go For</div>
    <div class="abs word" style="top:227px">Go-To</div>
    <div class="abs word" style="top:249px">In The Mood For</div>
    <div class="abs word" style="top:270px">Sip</div>
    <div class="abs word" style="top:291px">Soothing</div>
    <div class="abs word" style="top:312px">Stick With</div>
    <div class="abs word" style="top:334px">Throw In/Throw On</div>

    <div class="abs group-icon" style="top:360px"><svg width="12" height="14" viewBox="0 0 12 14"><rect x="1" y="6" width="10" height="8" rx="1" fill="#fff"/><path d="M3 6V4a3 3 0 0 1 6 0v2" stroke="#fff" stroke-width="1.6" fill="none"/></svg></div>
    <div class="abs group-title" style="top:367px">Long-Term Memory</div><div class="abs help" style="top:370px">?</div>
    <div class="abs word" style="top:394px">Give It A Try</div>
  </aside>

  <main class="abs content">
    <h1 class="abs h-progress">Word Progress</h1>
    <div class="abs track" style="left:60px;width:272px;background:var(--accent)"></div>
    <div class="abs track" style="left:332px;width:544px;background:var(--grey-step)"></div>
    <div class="abs step step--done" style="left:38px;top:70px">1</div>
    <div class="abs step step--current" style="left:309px;top:70px">2</div>
    <div class="abs step step--todo" style="left:582px;top:70px">3</div>
    <div class="abs step step--todo" style="left:854px;top:70px">4</div>
    <div class="abs step-label" style="left:32px">Review 1</div>
    <div class="abs step-label" style="left:298px">Review 2</div>
    <div class="abs step-label step-label--todo" style="left:578px">Review 3</div>
    <div class="abs step-label step-label--todo" style="left:847px">Review 4</div>
    <div class="abs btn-continue">Continue Review 3</div>

    <div class="abs btn-start"><svg width="10" height="11" viewBox="0 0 10 11"><path d="M0 0l10 5.5L0 11z" fill="#2a62b2"/></svg>Start Vocabulary Review Exercise 3</div>
    <div class="abs chip-word">Grab <svg width="14" height="14" viewBox="0 0 24 24"><path d="M12 1l3.4 7 7.6 1-5.5 5.3 1.3 7.7L12 18.3 5.2 22l1.3-7.7L1 9l7.6-1z" fill="#f5c518"/></svg></div>

    <p class="abs definition">The word "<b>grab</b>" is most commonly used as a <strong>verb</strong>, meaning <b>to take something quickly or suddenly</b>. Imagine you're running late for school. You don't have time for breakfast, so you <b>quickly</b> grab an apple from the kitchen and rush out the door. As you reach the bus stop, your friend waves and says, "Hey! Let's <b>grab</b> a coffee after class." Later, when you sit down, your phone starts ringing. You <b>grab</b> it from your bag and answer.</p>

    <h2 class="abs h-curve">Learning Curve Graph</h2>
    <div class="abs chart" role="img" aria-label="Bar chart of memory level for the word grab by date">
      <div class="abs band" style="top:0;height:63px;background:var(--band-long)"></div>
      <div class="abs band" style="top:63px;height:98px;background:var(--band-work)"></div>
      <div class="abs band" style="top:161px;height:45px;background:var(--band-short)"></div>
      <div class="abs band" style="top:206px;height:52px;background:var(--band-forgot)"></div>
      <div class="abs band-label" style="top:31px">Long-Term Memory</div>
      <div class="abs band-label" style="top:71px">Working Memory</div>
      <div class="abs band-label" style="top:168px">Short-Term Memory</div>
      <div class="abs band-label" style="top:214px">Forgotten Memory</div>
      <div class="abs bar bar--hit" style="left:100px;height:93px"></div>
      <div class="abs bar" style="left:142px;height:112px"></div>
      <div class="abs bar bar--hit" style="left:187px;height:190px"></div>
      <div class="abs bar" style="left:233px;height:137px"></div>
      <div class="abs bar" style="left:281px;height:153px"></div>
      <div class="abs bar" style="left:323px;height:112px"></div>
      <div class="abs bar" style="left:370px;height:75px"></div>
      <div class="abs bar" style="left:412px;height:203px"></div>
      <div class="abs bar" style="left:458px;height:153px"></div>
      <div class="abs bar" style="left:499px;height:225px"></div>
      <div class="abs bar" style="left:538px;height:131px"></div>
      <div class="abs bar" style="left:578px;height:153px"></div>
      <div class="abs bar" style="left:618px;height:192px"></div>
      <div class="abs bar" style="left:656px;height:94px"></div>
      <div class="abs bar" style="left:696px;height:131px"></div>
      <div class="abs bar" style="left:736px;height:177px"></div>
      <div class="abs bar" style="left:777px;height:119px"></div>
      <div class="abs bar" style="left:816px;height:216px"></div>
      <div class="abs tip" style="left:162px;top:24px">May 19</div>
      <div class="abs tip" style="left:76px;top:117px">May 18</div>
    </div>
    <div class="abs axis"><span>18 May</span><span>12:00</span><span>19 May</span><span>12:00</span><span>20 May</span><span>T 12:00</span><span>21 May</span><span>12:00</span><span>22 May</span><span>12:00</span><span>23 May</span><span>12:00</span><span>24 May</span><span>12:00</span><span>25 May</span><span>12:00</span><span>26 May</span><span>12:00</span><span>27 May</span><span>12:00</span><span>28...</span></div>
    <div class="abs axis-title">Date Range</div>

    <h2 class="abs h-analysis">WordNest Tutor Learning Analysis</h2>
    <p class="abs analysis">Lorem ipsum dolor sit amet, consectetur adipiscing elit. Nam rutrum commodo enim id bibendum. Nunc dignissim risus erat, nec finibus nunc dictum eu. Aliquam sit amet euismod metus, quis malesuada erat. Sed at felis quis nulla feugiat cursus at at dolor. Maecenas pretium aliquet dapibus. Fusce et eleifend massa. Sed convallis ex mi, at lobortis ligula congue vel.</p>
  </main>
</section>

<!-- ===== Expanded vocabulary view ===== -->
<section class="screen screen--popup">
  <div class="abs brand-name">QuillVane</div>
  <div class="abs topbar-title">WordNest Tutor<svg width="10" height="6" viewBox="0 0 10 6"><path d="M0 0h10L5 6z" fill="#fff"/></svg></div>
  <div class="abs topbar-icons"><span><i></i></span><span><i></i></span><span><i></i></span><span><i></i></span></div>
  <div class="abs search"><span>Search</span><span>⌕</span></div>

  <nav class="abs main-nav">
    <div class="nav-item nav-item--active">
      <svg width="28" height="26" viewBox="0 0 28 26"><path d="M14 1 1 13h4v12h7v-8h4v8h7V13h4z" fill="#2a62b2"/></svg>
      WordNest Tutor</div>
    <div class="nav-item">
      <svg width="32" height="30" viewBox="0 0 32 30"><path d="M1 8l9-3 10 3 8-3v22l-8 3-10-3-9 3z" fill="#fff"/><path d="M10 5v22M20 8v22" stroke="#4a80c2" stroke-width="2"/></svg>
      Daily English</div>
    <div class="nav-item nav-item--biz">
      <svg width="34" height="32" viewBox="0 0 34 32"><circle cx="13" cy="12" r="9" fill="none" stroke="#fff" stroke-width="5" stroke-dasharray="4 3"/><circle cx="13" cy="12" r="4" fill="#fff"/></svg>
      Business</div>
  </nav>

  <aside class="abs vocab-panel">
    <div class="abs filter">All</div>
    <div class="abs expand">Expand</div>
    <div class="abs group-title" style="top:73px">Short-Term Memory</div>
    <div class="abs word word--lead" style="top:99px">Grab</div>
    <div class="abs group-title" style="top:137px">Working Memory</div>
    <div class="abs word" style="top:164px">Cool Down</div>
    <div class="abs word" style="top:185px">Crave</div>
    <div class="abs word" style="top:206px">Go For</div>
  </aside>

  <main class="abs content">
    <h1 class="abs h-progress">Word Progress</h1>
    <div class="abs track" style="left:60px;width:272px;background:var(--accent)"></div>
    <div class="abs track" style="left:332px;width:544px;background:var(--grey-step)"></div>
    <div class="abs step step--done" style="left:38px;top:70px">1</div>
    <div class="abs step step--current" style="left:309px;top:70px">2</div>
    <div class="abs step step--todo" style="left:582px;top:70px">3</div>
    <div class="abs step step--todo" style="left:854px;top:70px">4</div>
    <div class="abs step-label" style="left:32px">Review 1</div>
    <div class="abs step-label" style="left:298px">Review 2</div>
    <div class="abs btn-continue">Continue Review 3</div>
    <div class="abs btn-start">Start Vocabulary Review Exercise 3</div>
    <div class="abs chip-word">Grab</div>
    <h2 class="abs h-analysis">WordNest Tutor Learning Analysis</h2>
    <p class="abs analysis">Lorem ipsum dolor sit amet, consectetur adipiscing elit. Nam rutrum commodo enim id bibendum. Nunc dignissim risus erat, nec finibus nunc dictum eu. Aliquam sit amet euismod metus, quis malesuada erat. Sed at felis quis nulla feugiat cursus at at dolor. Maecenas pretium aliquet dapibus. Fusce et eleifend massa. Sed convallis ex mi, at lobortis ligula congue vel.</p>
  </main>

  <div class="abs scrim"></div>

  <div class="abs modal" role="dialog" aria-label="All vocabulary">
    <div class="abs modal-frame"></div>
    <div class="abs filter">All <svg width="9" height="6" viewBox="0 0 9 6"><path d="M1 1l3.5 3.5L8 1" stroke="#fff" stroke-width="1.6" fill="none"/></svg></div>
    <svg class="abs close" width="20" height="20" viewBox="0 0 20 20"><path d="M2 2l16 16M18 2 2 18" stroke="#9a9a9a" stroke-width="3"/></svg>
    <div class="abs group-head" style="top:86px">Short-Term Memory</div>
    <div class="abs word-row" style="top:129px"><span>Grab</span></div>
    <div class="abs group-head" style="top:173px">Working Memory</div>
    <div class="abs word-row" style="top:216px"><span>Cool Down</span><span>Crave</span><span>Go For</span><span>Go-To</span><span>In The Mood For</span><span>Sip</span><span>Soothing</span><span>Stick With</span><span>Throw In/Throw On</span></div>
    <div class="abs group-head" style="top:263px">Long-Term Memory</div>
    <div class="abs word-row" style="top:306px"><span>Give It A Try</span></div>
  </div>
</section>

</body>
</html>
```